11th Annual Varmox Forum Flyer - Save the Date

We need a flyer for our annual Forum that will be creative with the theme of the Forum while highlighting our conference Title and Topics. Flyer should allow for a header that can be used consistently across conference communication. This is our 11th Annual Forum, which will take place outside of Houston, Texas at Brindle Hollow Resort and Spa.

Target Market(s)

Architects, engineers, contractors, universities, building project Owners

Industry/Entity Type

Construction

Font styles to use
Sans Serif

Colors

Designer to choose colors to be used in the design.

Requirements
Must have
• Title, date, location, key topics (title only), logo. See attached for breakdown of information.
Nice to have
• Creativity with the theme of the Forum, ability to slice flyer so that a portion can be used for a header in other conference documents.
• Mention of Closing Keynote, Dane Colvert
Should not have
• Please don't use the topic descriptions in the Flyer. Just the main titles of the topics is necessary.
• Should not be too word, but eye-catching with graphics and main

```html
<!DOCTYPE html>
<html lang="en">
<head>
<meta charset="UTF-8">
<title>11th Annual Varmox Forum</title>
<link href="https://fonts.googleapis.com/css2?family=Oswald:wght@500;700&family=Roboto:wght@400;500;700&display=swap" rel="stylesheet">
<style>
  :root {
    --brand-blue: #1f4190;
    --brand-green: #8db43c;
    --ink-gray: #555a5e;
    --paper: #ffffff;
    --paper-edge: #d9dadb;
  }
  * { margin: 0; padding: 0; box-sizing: border-box; }
  html, body { width: 927px; height: 1200px; overflow: hidden; }
  body { font-family: "Roboto", Arial, sans-serif; background: var(--brand-blue); }

  .flyer { position: relative; width: 927px; height: 1200px; overflow: hidden;
    background: radial-gradient(ellipse 70% 40% at 50% 22%, var(--paper) 40%, var(--paper-edge) 100%); }

  .brand { position: absolute; left: 52px; top: 56px; display: flex; flex-direction: column; align-items: center; width: 200px; }
  .brand-mark { width: 90px; height: 90px; border-radius: 50%; background: var(--brand-blue); }
  .brand-name { margin-top: 14px; font-family: "Roboto", Arial, sans-serif; font-weight: 400; font-size: 42px; color: var(--ink-gray); letter-spacing: -1px; }

  .event-info { position: absolute; left: 330px; top: 48px; width: 560px; color: #222; }
  .event-title { font-family: "Oswald", Impact, sans-serif; font-weight: 700; font-size: 66px; line-height: 1; color: var(--brand-blue); letter-spacing: -1px; }
  .event-title sup { font-size: 22px; vertical-align: 34px; margin-right: 6px; }
  .event-location { font-size: 15px; letter-spacing: 0.6px; margin: 4px 0 0 10px; }
  .event-line { margin-left: 10px; color: var(--brand-blue); font-size: 14.5px; margin-top: 4px; }
  .event-line strong { font-weight: 700; }
  .event-line .muted { color: #222; font-size: 12px; }
  .event-detail { margin-left: 10px; font-size: 12px; line-height: 1.25; color: #222; }

  .skyline { position: absolute; left: 0; top: 288px; width: 927px; height: 130px;
    background: linear-gradient(to bottom, rgba(31,65,144,0) 0%, rgba(31,65,144,0.55) 45%, var(--brand-blue) 100%); }
  .theme-band { position: absolute; left: 0; top: 418px; width: 927px; height: 782px; background: var(--brand-blue); }

  .theme-art { position: absolute; left: 0; top: 0; width: 927px; height: 1200px; }
  .headline { font-family: "Oswald", Impact, sans-serif; font-weight: 700; fill: var(--paper); }
  .headline-accent { font-family: "Oswald", Impact, sans-serif; font-weight: 700; fill: var(--brand-green); }
  .topic-title { font-family: "Oswald", Impact, sans-serif; font-weight: 500; fill: var(--brand-green); }
  .topic-sub { font-family: "Oswald", Impact, sans-serif; font-weight: 500; fill: var(--brand-green); }

  .stool { position: absolute; left: 470px; top: 880px; width: 320px; height: 320px;
    background: linear-gradient(to bottom, rgba(141,180,60,0.85), rgba(141,180,60,0.35)); border-radius: 40px 40px 0 0; }
</style>
</head>
<body>
<main class="flyer">
  <div class="brand">
    <div class="brand-mark"></div>
    <div class="brand-name">I-Varmox</div>
  </div>

  <section class="event-info">
    <h1 class="event-title">11<sup>TH</sup>ANNUAL FORUM</h1>
    <p class="event-location">Outside of Houston, Texas at Brindle Hollow Resort and Spa.</p>
    <p class="event-line"><strong>THURSDAY:</strong> OPENING KEYNOTE (Lunch Presentation)</p>
    <p class="event-line"><strong>FRIDAY:</strong> CLOSING KEYNOTE, DANE COLVERT, <span class="muted">author of (among others):</span></p>
    <p class="event-detail">“The Well Office Shift. How healthy people, culture, and building lead to high performance,” and, “The Building Owner’s Reset: Nine Practical Keys to Lowering Costs, Cutting Waste”</p>
    <p class="event-line">(Final Wrap-up) <span class="muted">- final wrap-up, discussion, and door prizes.</span></p>
  </section>

  <div class="skyline" role="img" aria-label="City skyline silhouette in brand blue"></div>
  <div class="theme-band"></div>

  <svg class="theme-art" viewBox="0 0 927 1200" aria-label="The Three Legged Stool? Balanced or Broken">
    <text class="headline" x="93" y="503" font-size="60" textLength="160" lengthAdjust="spacingAndGlyphs">THE</text>
    <text class="headline" x="90" y="660" font-size="192" textLength="744" lengthAdjust="spacingAndGlyphs">THREE</text>
    <text class="headline" x="90" y="785" font-size="142" textLength="464" lengthAdjust="spacingAndGlyphs">LEGGED</text>
    <text class="headline" x="585" y="745" font-size="90" textLength="244" lengthAdjust="spacingAndGlyphs">STOOL</text>
    <text class="headline-accent" x="578" y="862" font-size="140" textLength="50" lengthAdjust="spacingAndGlyphs">?</text>
    <text class="headline-accent" x="93" y="850" font-size="62" textLength="480" lengthAdjust="spacingAndGlyphs">Balanced or Broken</text>

    <g class="topics">
      <path d="M155 898 L178 890 L178 912 L155 920 Z" fill="#fff"/>
      <text class="topic-title" x="198" y="930" font-size="50" textLength="228" lengthAdjust="spacingAndGlyphs">THE RIGHT</text>
      <text class="topic-sub" x="198" y="958" font-size="22" textLength="246" lengthAdjust="spacingAndGlyphs">CONTRACT MANAGEMENT</text>

      <path d="M155 993 L178 985 L178 1007 L155 1015 Z" fill="#fff"/>
      <text class="topic-title" x="198" y="1025" font-size="50" textLength="228" lengthAdjust="spacingAndGlyphs">THE RIGHT</text>
      <text class="topic-sub" x="198" y="1051" font-size="22" textLength="88" lengthAdjust="spacingAndGlyphs">CULTURE</text>

      <path d="M155 1085 L178 1077 L178 1099 L155 1107 Z" fill="#fff"/>
      <text class="topic-title" x="198" y="1117" font-size="50" textLength="228" lengthAdjust="spacingAndGlyphs">THE RIGHT</text>
      <text class="topic-sub" x="198" y="1143" font-size="22" textLength="184" lengthAdjust="spacingAndGlyphs">SUBCONTRACTORS</text>
    </g>
  </svg>

  <div class="stool" role="img" aria-label="Green three-legged stool illustration"></div>
</main>
</body>
</html>
```